Tidewell-Network Theme For Forums!

We are looking for a theme for our forums. The forums are ran off Invision Power Boards. We have a basic theme on there now but we want more our own feel. If possible have some longboarding accept incorporated in the theme. We want the theme to have some red in it to match our logo. Tidewell-network.com

Target Market(s)

Skatingboarding & Longboarding

Coding

Coded - Design and coding required

Number of Pages Required

1 page

Colors
f04a50

```html
<!DOCTYPE html>
<html lang="en">
<head>
<meta charset="utf-8">
<title>Tidewell-Network Forums</title>
<link href="https://fonts.googleapis.com/css2?family=Montserrat:wght@400;500;600;700;800&family=Arimo:wght@400&display=swap" rel="stylesheet">
<style>
:root{
  --red:#e8303f;
  --red-deep:#c8101e;
  --red-nav:#f03a48;
  --pink:#fde0e3;
  --row:#f6f6f6;
  --line:#dcdcdc;
  --ink:#333;
  --ink-soft:#555;
  --footer:#3a3a3a;
  --grey-btn:#5b5b5b;
}
*{box-sizing:border-box;margin:0;padding:0}
html,body{width:1006px;height:1200px;overflow:hidden;background:#fff}
body{font-family:Arimo,Arial,sans-serif;color:var(--ink);font-size:11px;position:relative}
.head{height:87px;background:linear-gradient(#e02a37,var(--red-deep));position:relative}
.brand{position:absolute;left:24px;top:28px;color:#fff;font:800 24px Montserrat,sans-serif;display:flex;align-items:center;gap:8px}
.brand .mark{width:14px;height:14px;background:#fff}
.avatar{position:absolute;left:755px;top:14px;width:58px;height:58px;border-radius:50%;background:linear-gradient(#d7b9a4,#8a6a58);border:2px solid #f2f2f2}
.select{position:absolute;top:24px;height:20px;background:#c0101c;color:#fff;font-size:10px;padding:4px 6px}
.select::after{content:"";position:absolute;right:7px;top:8px;border:4px solid transparent;border-top-color:#fff}
.sel-user{left:823px;width:107px}
.sel-count{left:934px;width:56px}
.user-links{position:absolute;left:823px;top:55px;font-size:10px}
.user-links a{color:#fff;margin-right:15px}
.nav{height:43px;background:var(--red-nav);display:flex;justify-content:flex-end;align-items:center;padding-right:16px;gap:42px}
.nav a{color:#fff;text-decoration:none;font-size:10.5px}
.welcome{height:43px;background:var(--pink);text-align:center;line-height:43px;font:500 14px Montserrat,sans-serif;color:#444;letter-spacing:.3px}
.crumbs{position:absolute;top:192px;left:24px;font-size:10.5px;color:#333}
.crumbs span.sep{margin:0 14px}
.quick{position:absolute;top:192px;right:16px;font-size:10.5px;display:flex;gap:6px;align-items:center}
.rss{width:9px;height:9px;background:var(--red);border-radius:1px}
.pager{position:absolute;top:219px;left:24px;display:flex;align-items:center;gap:3px;font-size:9px;color:#555}
.pager .count{font-size:10.5px;margin-right:4px}
.pager b{font-weight:400;border:1px solid #bbb;height:20px;min-width:23px;padding:0 6px;display:flex;align-items:center;justify-content:center}
.pager b.plain{border:none}
.btn{position:absolute;top:219px;height:31px;color:#fff;font:500 10.5px Montserrat,sans-serif;display:flex;align-items:center;justify-content:center}
.btn-watch{left:758px;width:114px;background:var(--red)}
.btn-new{left:876px;width:114px;background:var(--grey-btn)}
.panel{position:absolute;left:23px;width:967px}
.cat{top:273px;border:1px solid var(--line)}
.cat-title{height:40px;background:var(--red);color:#fff;font:600 10.5px Montserrat,sans-serif;display:flex;align-items:center;justify-content:space-between;padding:0 14px}
.cat-title i{width:9px;height:9px;background:#fff;position:relative}
.cat-title i::after{content:"";position:absolute;left:2px;right:2px;top:4px;height:1px;background:var(--red)}
.grid-forum{display:grid;grid-template-columns:578px 80px 96px 1fr}
.grid-topic{display:grid;grid-template-columns:391px 144px 151px 223px 1fr}
.hrow{height:40px;background:var(--pink);font:600 10.5px Montserrat,sans-serif;color:#444}
.hrow>div,.drow>div{display:flex;align-items:center;justify-content:center;border-right:1px solid var(--line)}
.hrow>div:last-child,.drow>div:last-child{border-right:none}
.cat .hrow>div:first-child{justify-content:flex-start;padding-left:14px;font-size:12px;font-weight:500}
.drow{background:var(--row);border-top:1px solid var(--line)}
.cat .drow{height:72px}
.icon{width:26px;height:26px;border-radius:4px;background:linear-gradient(135deg,#f5b5ba,var(--red));transform:rotate(-40deg) scaleY(.45)}
.fcell{justify-content:flex-start!important;padding-left:14px;gap:14px}
.fname{font:500 11.5px Montserrat,sans-serif;color:#333;margin-bottom:6px}
.fdesc{font-size:9.5px}
.num{color:var(--red);font-size:9.5px;align-items:flex-start!important;padding-top:22px}
.lastinfo{justify-content:flex-start!important;padding-left:42px;font-size:9.5px;line-height:17px}
.lastinfo a{color:#333}
.lastinfo em{font-style:normal;display:inline-block;width:24px}
.topics{border:1px solid var(--line)}
.t1{top:437px}.t2{top:766px}
.topics .hrow>div:first-child{justify-content:flex-start;padding-left:59px}
.topics .drow{height:71.5px;font:500 9px Montserrat,sans-serif;color:#444}
.tcell{justify-content:flex-start!important;padding-left:6px;gap:16px}
.tcell .icon{flex:none}
.tag{background:var(--red);color:#fff;font:600 9px Montserrat,sans-serif;padding:3px 9px;margin-right:7px}
.ttitle{display:flex;align-items:center;font-size:9px;margin-bottom:11px}
.tdesc{font:400 10px Arimo,Arial,sans-serif;color:#333}
.stack{flex-direction:column;line-height:17px}
.arrow{display:inline-block;vertical-align:middle;margin-right:3px}
.check{width:15px;height:15px;border:1px solid #bbb;border-radius:4px;background:#fff}
.footer{position:absolute;top:1146px;left:0;width:1006px;height:54px;background:var(--footer);color:#fff;font-size:10px;text-align:center;line-height:54px}
.footer small{position:absolute;right:8px;bottom:4px;line-height:12px;font-size:10px}
</style>
</head>
<body>
<header class="head">
  <div class="brand"><span class="mark"></span>TIDEWELL-NETWORK</div>
  <div class="avatar" role="img" aria-label="Member profile photo"></div>
  <div class="select sel-user">John</div>
  <div class="select sel-count">0</div>
  <div class="user-links"><a href="#">Signout</a><a href="#">Help</a></div>
</header>
<nav class="nav"><a href="#">Help</a><a href="#">Search</a><a href="#">Members</a><a href="#">Calendar</a></nav>
<div class="welcome">WELCOME GUEST</div>

<div class="crumbs">The Ink Nib Network<span class="sep">›</span>Regional Focus<span class="sep">›</span>Penne Stilografich della Italia</div>
<div class="quick">INN Guidelines View New Content <span class="rss"></span></div>

<div class="pager"><span class="count">(54 Pages )</span><b>▾</b><b class="plain">1</b><b>2</b><b>3</b><b>→</b><b>Last &nbsp;&nbsp;»</b></div>
<div class="btn btn-watch">WATCH FORUM</div>
<div class="btn btn-new">START NEW TOPIC</div>

<section class="panel cat">
  <div class="cat-title">SED UT PERSPICIATIS UNDE<i></i></div>
  <div class="hrow grid-forum"><div>FORUM</div><div>TOPICS</div><div>REPLIES</div><div>LAST POST INFO</div></div>
  <div class="drow grid-forum">
    <div class="fcell"><span class="icon" role="img" aria-label="Longboard icon"></span><div><div class="fname">A TEST FORUM</div><div class="fdesc">A Test Forum That may be removed at any Time</div></div></div>
    <div class="num">1</div><div class="num">1</div>
    <div class="lastinfo"><div><div><em>▦</em>Apr 7 2006,07:52 PM</div><div><em>In :</em><a href="#">Welcome</a></div><div><em>By :</em><a href="#">Board Team</a></div></div></div>
  </div>
</section>

<section class="panel topics t1">
  <div class="hrow grid-topic"><div>TOPICS</div><div>STARTED &nbsp;BY</div><div>STATS</div><div>LAST POST INFO</div><div><span class="check"></span></div></div>
  <div class="drow grid-topic"><div class="tcell"><span class="icon" role="img" aria-label="Longboard icon"></span><div><div class="ttitle"><span class="tag">PINNED</span>SERVICING THE FILLER OF A VELOCE EXTRA FACETED</div><div class="tdesc">a guide with pictures........</div></div></div><div>RAVI 214</div><div class="stack"><span>1 REPLAY</span><span>95 VIEWS</span></div><div class="stack"><span><svg class="arrow" width="16" height="8"><path d="M0 4H14M10 1L14 4L10 7" stroke="#333" fill="none" stroke-width="1.3"/></svg>TODAY,01:31 PM</span><span>BY : DANIELT</span></div><div><span class="check"></span></div></div>
  <div class="drow grid-topic"><div class="tcell"><span class="icon" role="img" aria-label="Longboard icon"></span><div><div class="ttitle"><span class="tag">PINNED</span>ITALIAN BRANDS CONTACT INFO</div><div class="tdesc">a guide with pictures........</div></div></div><div>SKYLARK22</div><div class="stack"><span>1 REPLAY</span><span>95 VIEWS</span></div><div class="stack"><span><svg class="arrow" width="16" height="8"><path d="M0 4H14M10 1L14 4L10 7" stroke="#333" fill="none" stroke-width="1.3"/></svg>TODAY,01:31 PM</span><span>BY : DANIELT</span></div><div><span class="check"></span></div></div>
  <div class="drow grid-topic"><div class="tcell"><span class="icon" role="img" aria-label="Longboard icon"></span><div><div class="ttitle"><span class="tag">PINNED</span>THE MARLOW 88 DYNASTY</div><div class="tdesc">a guide with pictures........</div></div></div><div>RAVI 214</div><div class="stack"><span>1 REPLAY</span><span>95 VIEWS</span></div><div class="stack"><span><svg class="arrow" width="16" height="8"><path d="M0 4H14M10 1L14 4L10 7" stroke="#333" fill="none" stroke-width="1.3"/></svg>TODAY,01:31 PM</span><span>BY : DANIELT</span></div><div><span class="check"></span></div></div>
  <div class="drow grid-topic"><div class="tcell"><span class="icon" role="img" aria-label="Longboard icon"></span><div><div class="ttitle"><span class="tag">PINNED</span>LIST OF CURRENT PRODUCTION ITALIAN</div><div class="tdesc">a guide with pictures........</div></div></div><div>RAVI 214</div><div class="stack"><span>1 REPLAY</span><span>95 VIEWS</span></div><div class="stack"><span><svg class="arrow" width="16" height="8"><path d="M0 4H14M10 1L14 4L10 7" stroke="#333" fill="none" stroke-width="1.3"/></svg>TODAY,01:31 PM</span><span>BY : DANIELT</span></div><div><span class="check"></span></div></div>
</section>

<section class="panel topics t2">
  <div class="hrow grid-topic"><div>TOPICS</div><div>STARTED &nbsp;BY</div><div>STATS</div><div>LAST POST INFO</div><div><span class="check"></span></div></div>
  <div class="drow grid-topic"><div class="tcell"><span class="icon" role="img" aria-label="Longboard icon"></span><div><div class="ttitle"><span class="tag">PINNED</span>SERVICING THE FILLER OF A VELOCE EXTRA FACETED</div><div class="tdesc">a guide with pictures........</div></div></div><div>RAVI 214</div><div class="stack"><span>1 REPLAY</span><span>95 VIEWS</span></div><div class="stack"><span><svg class="arrow" width="16" height="8"><path d="M0 4H14M10 1L14 4L10 7" stroke="#333" fill="none" stroke-width="1.3"/></svg>TODAY,01:31 PM</span><span>BY : DANIELT</span></div><div><span class="check"></span></div></div>
  <div class="drow grid-topic"><div class="tcell"><span class="icon" role="img" aria-label="Longboard icon"></span><div><div class="ttitle"><span class="tag">PINNED</span>ITALIAN BRANDS CONTACT INFO</div><div class="tdesc">a guide with pictures........</div></div></div><div>SKYLARK22</div><div class="stack"><span>1 REPLAY</span><span>95 VIEWS</span></div><div class="stack"><span><svg class="arrow" width="16" height="8"><path d="M0 4H14M10 1L14 4L10 7" stroke="#333" fill="none" stroke-width="1.3"/></svg>TODAY,01:31 PM</span><span>BY : DANIELT</span></div><div><span class="check"></span></div></div>
  <div class="drow grid-topic"><div class="tcell"><span class="icon" role="img" aria-label="Longboard icon"></span><div><div class="ttitle"><span class="tag">PINNED</span>THE MARLOW 88 DYNASTY</div><div class="tdesc">a guide with pictures........</div></div></div><div>RAVI 214</div><div class="stack"><span>1 REPLAY</span><span>95 VIEWS</span></div><div class="stack"><span><svg class="arrow" width="16" height="8"><path d="M0 4H14M10 1L14 4L10 7" stroke="#333" fill="none" stroke-width="1.3"/></svg>TODAY,01:31 PM</span><span>BY : DANIELT</span></div><div><span class="check"></span></div></div>
  <div class="drow grid-topic"><div class="tcell"><span class="icon" role="img" aria-label="Longboard icon"></span><div><div class="ttitle"><span class="tag">PINNED</span>LIST OF CURRENT PRODUCTION ITALIAN</div><div class="tdesc">a guide with pictures........</div></div></div><div>RAVI 214</div><div class="stack"><span>1 REPLAY</span><span>95 VIEWS</span></div><div class="stack"><span><svg class="arrow" width="16" height="8"><path d="M0 4H14M10 1L14 4L10 7" stroke="#333" fill="none" stroke-width="1.3"/></svg>TODAY,01:31 PM</span><span>BY : DANIELT</span></div><div><span class="check"></span></div></div>
</section>

<footer class="footer">© Copyright-2018 Tidewell-Network.All rights reserved.<small>C2</small></footer>
</body>
</html>
```